Veltrane Group Business Card Design

The CEO is looking for a new trendy look for his business card.
You can stay with current branding or come up with something new/creative. It can be 3D, including Medical Office buildings. You can use our logo in a variety of colors. Please include name, title, company name, company website, email address, cell number

Target Market(s)

Real Estate Development and Construction

Industry/Entity Type

Health care real estate

Contact Information for Business Card

Rohesh Kamdar, CEO M-604.781.2249 E-roheshkamdar@veltrane.com Address:4180 Lindqvist Ave, Halvern City, HV 33482 www.veltrane.com

Font styles to use
Other font styles liked:
• Be creative

Requirements
Must have
• Creative, trendy look
Nice to have
• Please go to our website to get a feel- www. veltrane.com
Should not have
• small fonts

```html
<!DOCTYPE html>
<html lang="en">
<head>
<meta charset="utf-8">
<title>Veltrane Group – Business Card</title>
<link href="https://fonts.googleapis.com/css2?family=Montserrat:wght@400;700;800&display=swap" rel="stylesheet">
<style>
  :root {
    --bg: #cfd5d5;
    --paper: #eeeeec;
    --brand-red: #b31f29;
    --text-grey: #444446;
    --edge-red: #c21e25;
    --shadow: rgba(40, 50, 50, 0.28);
  }
  * { margin: 0; padding: 0; box-sizing: border-box; }
  html, body { width: 1200px; height: 881px; overflow: hidden; }
  body {
    background: var(--bg);
    font-family: "Montserrat", Arial, sans-serif;
    position: relative;
  }
  .card {
    position: absolute;
    width: 520px;
    height: 298px;
    background: var(--paper);
    border-bottom: 6px solid var(--edge-red);
    box-shadow: 0 18px 40px var(--shadow);
  }
  .card--back { left: 50px; top: 300px; }
  .card--front { left: 630px; top: 300px; }

  .wordmark {
    color: var(--brand-red);
    font-weight: 800;
    letter-spacing: -1px;
    white-space: nowrap;
  }
  .card--front .wordmark {
    position: absolute;
    left: 0; right: 0; top: 50%;
    transform: translateY(-50%);
    text-align: center;
    font-size: 56px;
  }
  .card--back .wordmark {
    position: absolute;
    top: 40px; right: 44px;
    font-size: 40px;
  }

  .contact-row {
    position: absolute;
    top: 136px; left: 24px; right: 24px;
    display: flex;
    align-items: center;
    gap: 18px;
  }
  .identity { text-align: right; width: 190px; }
  .identity__name {
    color: var(--brand-red);
    font-weight: 700;
    font-size: 19px;
    letter-spacing: 0.5px;
  }
  .identity__title {
    color: var(--text-grey);
    font-size: 16px;
    margin-top: 4px;
  }
  .divider { width: 1.5px; height: 76px; background: var(--brand-red); }
  .details { list-style: none; }
  .details li {
    display: flex; align-items: center; gap: 8px;
    color: var(--text-grey);
    font-size: 13.5px;
    line-height: 24px;
    white-space: nowrap;
  }
  .details svg { width: 12px; height: 12px; flex: none; }
  .address {
    position: absolute;
    bottom: 34px; left: 0; right: 0;
    text-align: center;
    color: var(--text-grey);
    font-size: 14.5px;
  }
</style>
</head>
<body>
  <section class="card card--back" aria-label="Card back with contact details">
    <div class="wordmark">Veltrane Group</div>
    <div class="contact-row">
      <div class="identity">
        <div class="identity__name">ROHESH KAMDAR</div>
        <div class="identity__title">CEO</div>
      </div>
      <div class="divider"></div>
      <ul class="details">
        <li>
          <svg viewBox="0 0 12 12" aria-hidden="true"><rect x="3" y="0.5" width="6" height="11" rx="1" fill="none" stroke="#b31f29" stroke-width="1.2"/><circle cx="6" cy="9.5" r="0.7" fill="#b31f29"/></svg>
          604.781.2249
        </li>
        <li>
          <svg viewBox="0 0 12 12" aria-hidden="true"><rect x="0.5" y="2.5" width="11" height="7.5" fill="#b31f29"/><path d="M0.5 2.5 L6 7 L11.5 2.5" fill="none" stroke="#eeeeec" stroke-width="1"/></svg>
          roheshkamdar@veltrane.com
        </li>
        <li>
          <svg viewBox="0 0 12 12" aria-hidden="true"><circle cx="6" cy="6" r="5.5" fill="#b31f29"/><path d="M0.5 6 H11.5 M6 0.5 V11.5" stroke="#eeeeec" stroke-width="0.8"/></svg>
          www.veltrane.com
        </li>
      </ul>
    </div>
    <div class="address">4180 Lindqvist Ave, Halvern City, HV 33482</div>
  </section>

  <section class="card card--front" aria-label="Card front">
    <div class="wordmark">Veltrane Group</div>
  </section>
</body>
</html>
```